Etikett für einen Rosé Wein
Zielgruppe
Wir sind ein Weingut und benötigen ein neues Etikett für unseren Muskattrollinger Rosé. Unsere Kunden sind eher traditionelle Weinkäufer.
Aufgabenstellung
Format:
Höhe: 9 cm
Breite: 11 cm
Da es nur ein Vorderetikett gibt, müssen alle relevanten Angaben (Hersteller, Alkohol, Inhalt in L, Rebsorte, etc.) enthalten sein. (siehe Flaschenabbildung anbei)
WÜRTTEMBERG
2019er
Muskattrollinger Rosé
DEUTSCHER QUALITÄTSWEIN
11,0 % Vol.
0,75 l
Enthält Sulfite
A.P.Nr. 58127364
Abfüller
Straße / PLZ / Ort / Tel.
Der Flaschenverschluss ist schwarz d.h. das neue Etikettendesign sollte dazu passen.
Bisher ist der Hintergrund des Weinetiketts schwarz. Dies muss jedoch nicht so bleiben.
Im Anhang finden Sie außerdem ein Plakat. Ggf. können Sie für das Flaschendesign einige nostalgische Elemente davon übernehmen.

```html
<!DOCTYPE html>
<html lang="de">
<head>
<meta charset="utf-8">
<title>Muskattrollinger Rosé – Etikett</title>
<link rel="stylesheet" href="https://fonts.googleapis.com/css2?family=Sorts+Mill+Goudy&family=Great+Vibes&display=swap">
<style>
  :root {
    --stage: #3a2419;
    --label: #262628;
    --label-light: #323234;
    --accent: #c9521f;
    --accent-dark: #a8421a;
    --ink: #ffffff;
    --ink-soft: #f1ece6;
    --grape: #8e4a36;
    --leaf: #9a9a9a;
  }
  * { margin: 0; padding: 0; box-sizing: border-box; }
  html, body { width: 1100px; height: 1200px; overflow: hidden; }
  body {
    background: var(--stage);
    font-family: "Sorts Mill Goudy", Georgia, serif;
    position: relative;
  }
  .label {
    position: absolute;
    left: 50px; top: 190px;
    width: 1000px; height: 820px;
    background: radial-gradient(ellipse at 40% 45%, var(--label-light), var(--label) 70%);
    overflow: hidden;
    color: var(--ink);
  }
  .brush-band { position: absolute; left: 0; top: 86px; width: 880px; height: 90px; }
  .grape-art {
    position: absolute; right: 0; top: 0;
    width: 310px; height: 480px;
    background:
      radial-gradient(ellipse at 55% 62%, var(--grape) 0 38%, transparent 62%),
      linear-gradient(200deg, var(--leaf) 0%, rgba(154,154,154,0.35) 40%, transparent 70%);
  }
  .region {
    position: absolute; left: 0; width: 1006px; top: 66px;
    text-align: center; font-size: 64px; letter-spacing: 1px; color: var(--ink);
  }
  .vintage {
    position: absolute; left: 556px; top: 144px;
    font-size: 35px; color: var(--accent);
  }
  .variety {
    position: absolute; left: 215px; top: 190px;
    font-family: "Great Vibes", cursive;
    font-size: 118px; line-height: 1; color: var(--ink);
  }
  .variety-rose {
    position: absolute; left: 490px; top: 300px;
    font-family: "Great Vibes", cursive;
    font-size: 118px; line-height: 1; color: var(--ink);
  }
  .quality {
    position: absolute; left: 0; width: 1000px; top: 478px;
    text-align: center; font-size: 31px; line-height: 45px;
    color: var(--accent); letter-spacing: 0.5px;
  }
  .bottler {
    position: absolute; left: 0; width: 1000px; top: 632px;
    text-align: center; font-size: 25px; line-height: 38px; color: var(--ink-soft);
  }
  .bottler .marketer { color: var(--accent); font-size: 23px; }
  .alcohol {
    position: absolute; left: 56px; top: 673px;
    font-size: 28px; line-height: 38px; color: var(--ink-soft);
  }
  .alcohol .sulfite { display: block; color: var(--accent); font-size: 22px; }
  .volume {
    position: absolute; right: 56px; top: 670px;
    font-size: 38px; color: var(--ink-soft);
  }
  .address {
    position: absolute; left: 0; width: 1000px; top: 760px;
    text-align: center; font-size: 25px; color: var(--ink-soft);
  }
  .address .dot { color: var(--accent); padding: 0 8px; }
</style>
</head>
<body>
  <main class="label">
    <div class="grape-art" role="img" aria-label="Gezeichnete Rebranke mit Weinblatt und rötlicher Traube"></div>

    <svg class="brush-band" viewBox="0 0 880 90" aria-hidden="true">
      <polygon points="0,12 210,10 230,4 880,2 660,12 640,40 600,46 560,62 520,58 0,54" fill="var(--accent)"/>
      <polygon points="0,60 560,64 600,70 0,74" fill="var(--accent-dark)"/>
    </svg>

    <h1 class="region">Württemberg</h1>
    <p class="vintage">2019 er</p>
    <p class="variety">Muskattrollinger</p>
    <p class="variety-rose">Rosé</p>

    <p class="quality">DEUTSCHER<br>QUALITÄTSWEIN</p>

    <p class="alcohol">11,0% Vol.<span class="sulfite">Enthalten Sulfit</span></p>

    <p class="bottler">
      A.P.Nr. 581 273 64<br>
      Abfüller D-BWW 581<br>
      <span class="marketer">vermarkted durch: Lukas Brenner</span>
    </p>

    <p class="volume">0,75 l</p>

    <p class="address">Kelterweg 5<span class="dot">•</span>D-71562 Rebenau - Talhofen<span class="dot">•</span>Tel. 071 44/5550172</p>
  </main>
</body>
</html>
```